New business card design

I need original, modern, business looking but dzen (minimalistic) looking design.
Also refer to websit travenko.ru

Text is

Веденин Олег, PMP
Партнер

Моб. +7 (915) 604 7189
info@travenko.ru
Казань, Россия, 420111, ул. Берёзовая 27/2
=====================

Vedenin Oleg, PMP
Partner

Mob. +7 (915) 604 7189
info@travenko.ru
Moscow, Russia,125493, Beryozovaya 27/2

```html
<!DOCTYPE html>
<html lang="ru">
<head>
<meta charset="utf-8">
<title>Travenko — визитная карточка</title>
<link rel="stylesheet" href="https://fonts.googleapis.com/css2?family=Roboto+Condensed:wght@300;400;700&display=swap">
<style>
  :root {
    --page-bg: #e9ecef;
    --card-bg: #ffffff;
    --brand-cyan: #29b6d8;
    --brand-cyan-soft: #8fd8ea;
    --brand-blue: #1c7fc4;
    --text-grey: #4a4f55;
    --card-shadow: 0 10px 30px rgba(20, 30, 40, 0.18);
  }
  * { box-sizing: border-box; margin: 0; padding: 0; }
  html, body {
    width: 1200px;
    height: 900px;
    overflow: hidden;
    background: var(--page-bg);
    font-family: "Roboto Condensed", "Arial Narrow", sans-serif;
  }
  .canvas { position: relative; width: 1200px; height: 900px; }

  .card {
    position: absolute;
    left: 290px;
    width: 620px;
    height: 350px;
    background: var(--card-bg);
    box-shadow: var(--card-shadow);
    overflow: hidden;
  }

  .corner-pattern {
    position: absolute; right: 0; top: 0;
    background: radial-gradient(ellipse at 100% 0%, var(--brand-cyan) 0%, var(--brand-cyan-soft) 42%, rgba(255,255,255,0) 72%);
  }

  /* Front side */
  .card--front { top: 60px; }
  .card--front .corner-pattern { width: 190px; height: 240px; }
  .brand {
    position: absolute; left: 210px; top: 150px;
    display: flex; align-items: center; gap: 14px;
  }
  .brand__mark { width: 30px; height: 30px; background: var(--brand-cyan); }
  .brand__name {
    font-weight: 300; font-size: 46px; letter-spacing: 0.5px;
    color: var(--brand-cyan); line-height: 1;
  }

  /* Back side */
  .card--back { top: 490px; }
  .card--back .corner-pattern { width: 300px; height: 160px; }
  .person { position: absolute; right: 40px; top: 150px; text-align: left; }
  .person__name {
    font-weight: 700; font-size: 30px; color: var(--brand-cyan); line-height: 1.1;
  }
  .person__role {
    margin-top: 2px; font-size: 17px; color: var(--text-grey); letter-spacing: 0.5px;
  }
  .contacts {
    position: absolute; left: 40px; bottom: 36px;
    list-style: none; font-size: 15px; color: var(--brand-cyan); line-height: 1.7;
  }
  .contacts__item { display: flex; align-items: center; gap: 8px; }
  .contacts__bullet { width: 8px; height: 8px; background: var(--brand-blue); flex: none; }
</style>
</head>
<body>
<main class="canvas">
  <section class="card card--front" aria-label="Лицевая сторона">
    <div class="corner-pattern" role="img" aria-label="Декоративный узор из голубых квадратов"></div>
    <div class="brand">
      <span class="brand__mark"></span>
      <span class="brand__name">Travenko</span>
    </div>
  </section>

  <section class="card card--back" aria-label="Оборотная сторона">
    <div class="corner-pattern" role="img" aria-label="Декоративный узор из голубых квадратов"></div>
    <div class="person">
      <p class="person__name">Веденин Олег, PMP</p>
      <p class="person__role">Партнер</p>
    </div>
    <ul class="contacts">
      <li class="contacts__item"><span class="contacts__bullet"></span>Моб. +7 (915) 604 7189</li>
      <li class="contacts__item"><span class="contacts__bullet"></span>info@travenko.ru</li>
      <li class="contacts__item"><span class="contacts__bullet"></span>Казань, Россия, 420111, ул. Берёзовая 27/2</li>
    </ul>
  </section>
</main>
</body>
</html>
```